Designer Instructions – Updated Referral Program Flyer

(Based on the mock-up in “Brief Layout and Instructions.pdf”)

OVERALL STYLE + LAYOUT

Maintain the same general layout, structure, and flow as the mock-up flyer (front and back).

This is an update of an older flyer, not a full redesign — keep the same sections, proportions, and overall visual feel, but with cleaner, more modern design improvements.

The final flyer should look clean, bold, professional, and high-impact, geared toward realtors, property managers, and contractors who refer work.

FRONT SIDE INSTRUCTIONS
1. Header Section

Remove the Rebuild Harbor Crest logo from the top banner.
(Shown on page 1 of the PDF)

2. Main Headline

Keep the same three-line structure:
EARN
UNLIMITED
CASH

Center it, maximize impact, and increase the font size of CASH so all three words match in importance.

Make the headline bold, clean, and the main focal point.

3. Cash Incentive Box

Keep the "$500 minimum OR 10% per referral" box, but upgrade the graphics to look sharper and more modern.

Ensure the wording matches exactly what’s in the mock-up.

4. Premier Partner Program Ribbon

Clean up and modernize the "PREMIER PARTNER PROGRAM" bar while keeping the same position and structure.

Ensure the checkmark badge remains crisp and professional.

5. Supporting Icons Section

Keep the four icons/benefit boxes (Guaranteed Payout, Free Evaluations, Affordable Solutions, Industry Leaders) in the same order.

Update the icons to cleaner, more modern styles — but maintain the same meanings.

Improve alignment and spacing for sharper visual consistency.

6. Remove Icons in Contact Area

At the bottom (“CALL TEXT OR BOOK ONLINE 858-471-6093 BrightlaneRenovate.com”), remove the phone and internet icons, as noted on page 2 of the PDF.

7. Replace All Images

I (Dorian) will provide all updated stock images separately via email.

Replace the flood/water-damage imagery and roof leak with the new images I send.

Keep image placement and proportions the same as the mock-up.

BACK SIDE INSTRUCTIONS
1. Header Image + “REFER / EARN” Section

Maintain the same large split-image layout (“The more you refer, the more you earn”).

Replace all background imagery with the new assets I will send.

Keep the CASH FLOW image section but modernize the type and spacing.

2. “HOW IT WORKS” Section

Preserve the three-column layout:

Refer Flood, Water & Mold Damage

We Take Care of Everything (evaluations/insurance)

Get Paid to Share

Update images, tighten spacing, and use modern iconography.

3. Remove Phone/Internet Icons

Same as the front side — remove small communication icons and keep only the text/number/URL.

4. Bottom Contact Bar

Keep the blue bar, same wording, same layout — just modernize the style if needed for clarity.

5. Replace All Back-Side Images

Again, I will email you the image assets.

Keep the layout EXACT — just update with higher-quality photos and improved design.

TEXT CONTENT (Keep as-is unless spacing adjustments needed)

All text shown in the PDF should remain exactly the same unless spacing or visual balance requires minor adjustments.
Example from page 3:

“REFER FLOOD, MOLD & CONSTRUCTION JOBS”

“We Schedule a Free Estimate. If Approved, You Get Paid.”

“Everybody Benefits From Referrals”

Everything stays, just refreshed and visually improved.

DESIGN GOALS

Flyer should look high-end and trustworthy, not salesy.

Consistent color theme: blues, whites, yellows, same palette as original.

Use bold, modern fonts with strong readability.

Ensure all headlines pop and all benefit boxes are clean, well-aligned, and evenly spaced.

The final result should feel like a premium referral program flyer for a top-tier restoration/remodel company.

FILES I WILL PROVIDE

I will send the designer:

All replacement stock photos

Any updated logos (if needed)

Original high-resolution version of the mock-up (if available)

Any additional icons preferred

Colors
0054AA
0677BA
7BADD7
CADEEF
E8F1F8

Requirements
Must have
• Designer Instructions – Updated Referral Program Flyer (Based on the mock-up in “Brief Layout and Instructions.pdf”) OVERALL STYLE + LAYOUT Maintain the same general layout, structure, and flow as the mock-up flyer (front and back). This is an update of an older flyer, not a full redesign — keep the same sections, proportions, and overall visual feel, but with cleaner, more modern design improvements. The final flyer should look clean, bold, professional, and high-impact, geared toward realtors, property managers, and contractors who refer work. FRONT SIDE INSTRUCTIONS 1. Header Section Remove the Rebuild Harbor Crest logo from the top banner. (Shown on page 1 of the PDF) 2. Main Headline Keep the same three-line structure: EARN UNLIMITED CASH Center it, maximize impact, and increase the font size of CASH so all three words match in importance. Make the headline bold, clean, and the main focal point. 3. Cash Incentive Box Keep the "$500 minimum OR 10% per referral" box, but upgrade the graphics to look sharper and more modern. Ensure the wording matches exactly what’s in the mock-up. 4. Premier Partner Program Ribbon Clean up and modernize the "PREMIER PARTNER PROGRAM" bar while keeping the same position and structure. Ensure the checkmark badge remains crisp and professional. 5. Supporting Icons Section Keep the four icons/benefit boxes (Guaranteed Payout, Free Evaluations, Affordable Solutions, Industry Leaders) in the same order. Update the icons to cleaner, more modern styles — but maintain the same meanings. Improve alignment and spacing for sharper visual consistency. 6. Remove Icons in Contact Area At the bottom (“CALL TEXT OR BOOK ONLINE 858-471-6093 BrightlaneRenovate.com”), remove the phone and internet icons, as noted on page 2 of the PDF. 7. Replace All Images I (Dorian) will provide all updated stock images separately via email. Replace the flood/water-damage imagery and roof leak with the new images I send. Keep image placement and proportions the same as the mock-up. BACK SIDE INSTRUCTIONS 1. Header Image + “REFER / EARN” Section Maintain the same large split-image layout (“The more you refer, the more you earn”). Replace all background imagery with the new assets I will send. Keep the CASH FLOW image section but modernize the type and spacing. 2. “HOW IT WORKS” Section Preserve the three-column layout: Refer Flood, Water & Mold Damage We Take Care of Everything (evaluations/insurance) Get Paid to Share Update images, tighten spacing, and use modern iconography. 3. Remove Phone/Internet Icons Same as the front side — remove small communication icons and keep only the text/number/URL. 4. Bottom Contact Bar Keep the blue bar, same wording, same layout — just modernize the style if needed for clarity. 5. Replace All Back-Side Images Again, I will email you the image assets. Keep the layout EXACT — just update with higher-quality photos and improved design. TEXT CONTENT (Keep as-is unless spacing adjustments needed) All text shown in the PDF should remain exactly the same unless spacing or visual balance requires minor adjustments. Example from page 3: “REFER FLOOD, MOLD & CONSTRUCTION JOBS” “We Schedule a Free Estimate. If Approved, You Get Paid.” “Everybody Benefits From Referrals” Everything stays, just refreshed and visually improved. DESIGN GOALS Flyer should look high-end and trustworthy, not salesy. Consistent color theme: blues, whites, yellows, same palette as original. Use bold, modern fonts with strong readability. Ensure all headlines pop and all benefit boxes are clean, well-aligned, and evenly spaced. The final result should feel like a premium referral program flyer for a top-tier restoration/remodel company. FILES I WILL PROVIDE I will send the designer: All replacement stock photos Any updated logos (if needed) Original high-resolution version of the mock-up (if available) Any additional icons preferred

```html
<!DOCTYPE html>
<html lang="en">
<head>
<meta charset="utf-8">
<title>Premier Partner Program – Referral Flyer</title>
<link rel="stylesheet" href="https://fonts.googleapis.com/css2?family=Montserrat:wght@300;400;500;600;700;800&family=Anton&display=swap">
<style>
  :root {
    --backdrop: #8eadd6;
    --navy: #0b2a64;
    --ink: #0a1426;
    --yellow: #ffe600;
    --orange: #f7a21b;
    --red: #e42328;
    --slate: #7b8b97;
    --mist: #e9e9ec;
    --panel: #efeff1;
    --text: #333a40;
    --white: #ffffff;
    --sans: "Montserrat", Arial, sans-serif;
    --condensed: "Anton", "Impact", sans-serif;
  }
  * { margin: 0; padding: 0; box-sizing: border-box; }
  html, body { width: 958px; height: 1200px; overflow: hidden; }
  body { background: var(--backdrop); font-family: var(--sans); position: relative; }

  .card { position: absolute; left: 101px; width: 757px; height: 490px; background: var(--white); overflow: hidden; }
  .card--front { top: 97px; }
  .card--back { top: 614px; height: 489px; }
  .abs { position: absolute; }

  /* FRONT */
  .front-band { left: 0; top: 0; width: 757px; height: 195px; background: var(--navy); }
  .hero-photo { left: 0; top: 0; width: 757px; height: 195px; }
  .headline { left: 43px; top: 24px; width: 320px; text-align: center; font-weight: 800; line-height: 1; letter-spacing: -1.5px; }
  .headline span { display: block; font-size: 47px; }
  .headline .earn { color: var(--white); }
  .headline .unlimited { color: var(--yellow); margin-top: -3px; }
  .headline .cash { color: var(--yellow); margin-top: -3px; }

  .tagline { left: 43px; top: 170px; width: 318px; height: 44px; background: var(--yellow); color: var(--navy);
    font-weight: 600; font-size: 19.5px; display: flex; align-items: center; justify-content: center; letter-spacing: -0.3px; white-space: nowrap; }
  .offer { top: 223px; height: 47px; background: var(--red); color: var(--white); display: flex; align-items: center; }
  .offer--min { left: 43px; width: 152px; padding-left: 14px; }
  .offer--pct { left: 210px; width: 153px; padding-left: 24px; }
  .offer .amount { font-weight: 800; font-size: 30px; letter-spacing: -1px; }
  .offer .note { color: var(--yellow); font-size: 9.5px; font-weight: 500; line-height: 1.15; margin-left: 5px; }
  .offer-or { left: 193px; top: 236px; width: 20px; height: 20px; border-radius: 50%; background: var(--white); color: var(--red);
    font-weight: 800; font-size: 9px; display: flex; align-items: center; justify-content: center; border: 2px solid var(--red); }

  .premier { left: 373px; top: 170px; width: 346px; height: 25px; background: var(--mist); color: var(--red);
    font-size: 12px; font-weight: 500; letter-spacing: 8px; text-align: center; line-height: 25px; padding-left: 8px; }
  .program-bar { left: 373px; top: 195px; width: 346px; height: 61px; display: flex; }
  .program-bar div { flex: 1; color: var(--white); font-weight: 600; font-size: 23px; display: flex; align-items: center; }
  .program-bar .left { background: var(--red); padding-left: 18px; }
  .program-bar .right { background: var(--slate); justify-content: flex-end; padding-right: 14px; }
  .badge { left: 526px; top: 205px; width: 37px; height: 41px; }

  .wins { left: 42px; top: 290px; color: var(--navy); font-weight: 700; font-size: 18.5px; letter-spacing: -0.3px; }
  .benefit { top: 322px; width: 161px; height: 83px; padding: 11px 0 0 14px; }
  .benefit--grey { background: var(--mist); }
  .benefit--framed { border: 1.5px solid var(--yellow); background: var(--white); }
  .benefit h3 { font-size: 12px; font-weight: 600; line-height: 1.13; color: var(--text); }
  .benefit p { font-size: 9.8px; font-weight: 300; line-height: 1.38; color: var(--text); margin-top: 7px; white-space: nowrap; }
  .benefit p b { color: var(--red); font-weight: 600; }
  .benefit svg { position: absolute; right: 10px; top: 10px; width: 23px; height: 23px; }

  .slogan { left: 43px; top: 421px; color: var(--red); font-weight: 600; font-size: 16.5px; line-height: 1.23; letter-spacing: -0.2px; }
  .contact { left: 402px; top: 418px; width: 314px; height: 45px; border: 1px solid #9fb0c8; display: flex; }
  .contact .label { width: 112px; background: var(--navy); color: var(--white); font-size: 11.5px; font-weight: 500; line-height: 1.15;
    padding-left: 11px; display: flex; align-items: center; }
  .contact .lines { padding: 4px 0 0 17px; }
  .contact .phone { font-size: 16.5px; font-weight: 600; color: var(--text); line-height: 1.2; }
  .contact .web { font-size: 11.5px; font-weight: 600; color: var(--text); margin-top: 1px; }

  /* BACK */
  .back-band { left: 0; top: 0; width: 757px; height: 351px; background: var(--navy); }
  .cash-photo { left: 0; top: 0; width: 757px; height: 192px; }
  .refer-shadow { left: 0; top: 0; width: 757px; height: 230px; }
  .refer-stack { left: 71px; top: 33px; width: 116px; font-family: var(--condensed); text-transform: uppercase; line-height: 1; white-space: nowrap; text-align: left; font-weight: 400; }
  .refer-stack .small { display: block; color: var(--white); font-size: 19.5px; letter-spacing: -0.3px; }
  .refer-stack .big { display: block; font-size: 50px; letter-spacing: -0.5px; line-height: 0.98;
    background: linear-gradient(180deg, var(--yellow) 35%, var(--orange) 100%); -webkit-background-clip: text; background-clip: text; color: transparent; }
  .how { left: 266px; top: 132px; width: 224px; height: 48px; background: var(--red); color: var(--white);
    font-weight: 600; font-size: 25px; display: flex; align-items: center; justify-content: center; letter-spacing: -0.3px; }

  .step { top: 226px; width: 194px; height: 233px; background: var(--panel); border: 1px solid var(--navy); border-top: none; }
  .step .photo { width: 100%; height: 125px; display: block; }
  .step h4 { font-size: 12.5px; font-weight: 600; color: var(--text); text-align: center; line-height: 1.3; margin-top: 10px; }
  .step p { font-size: 11px; font-weight: 300; color: var(--text); text-align: center; line-height: 1.35; margin-top: 6px; }
  .step p b { color: var(--red); font-weight: 600; }
</style>
</head>
<body>

<!-- FRONT SIDE -->
<section class="card card--front">
  <div class="abs front-band"></div>
  <svg class="abs hero-photo" viewBox="0 0 757 195" role="img" aria-label="Photo of blue air movers and dehumidifiers drying a finished basement after a flood">
    <defs>
      <linearGradient id="basement" x1="0" y1="0" x2="1" y2="1">
        <stop offset="0" stop-color="#c9c4bb"/>
        <stop offset="0.55" stop-color="#a7a39c"/>
        <stop offset="1" stop-color="#4f8fb2"/>
      </linearGradient>
    </defs>
    <polygon points="480,0 757,0 757,195 505,195 397,84" fill="url(#basement)" stroke="#ffffff" stroke-width="3"/>
  </svg>

  <h1 class="abs headline">
    <span class="earn">EARN</span>
    <span class="unlimited">UNLIMITED</span>
    <span class="cash">CASH</span>
  </h1>

  <div class="abs tagline">GET PAID TO REFER A FLOOD</div>
  <div class="abs offer offer--min"><span class="amount">$500</span><span class="note">MINIMUM</span></div>
  <div class="abs offer offer--pct"><span class="amount">10%</span><span class="note">PER<br>REFERRAL!</span></div>
  <div class="abs offer-or">OR</div>

  <div class="abs premier">PREMIER</div>
  <div class="abs program-bar"><div class="left">PARTNER</div><div class="right">PROGRAM</div></div>
  <svg class="abs badge" viewBox="0 0 37 41" aria-hidden="true">
    <path d="M18.5 1 L35 6 V20 C35 30 27 37 18.5 40 C10 37 2 30 2 20 V6 Z" fill="#ffffff"/>
    <path d="M10 20 L16.5 27 L28 12" fill="none" stroke="#e42328" stroke-width="5" stroke-linecap="round" stroke-linejoin="round"/>
  </svg>

  <h2 class="abs wins">PARTNER WITH US &amp; EVERYBODY WINS!</h2>

  <div class="abs benefit benefit--grey" style="left:43px">
    <h3>GUARANTEED<br>PAYOUT</h3>
    <p>Minimum <b>$500</b> or <b>10%</b> of<br>Total Invoice Paid Fast.</p>
    <svg viewBox="0 0 24 24" aria-hidden="true"><rect x="6" y="3" width="16" height="10" rx="1.5" fill="none" stroke="#e42328" stroke-width="1.8"/><circle cx="14" cy="8" r="2" fill="#e42328"/><path d="M2 14 L9 14 L13 17 L8 22 L2 22 Z" fill="#e42328"/></svg>
  </div>
  <div class="abs benefit benefit--framed" style="left:214px">
    <h3>FREE<br>ESTIMATES</h3>
    <p>Fast and Free Inspections<br>and Written Estimates.</p>
    <svg viewBox="0 0 24 24" aria-hidden="true"><rect x="3" y="4" width="18" height="18" rx="1.5" fill="none" stroke="#e42328" stroke-width="1.8"/><rect x="8" y="2" width="8" height="4" fill="#e42328"/><path d="M7 11h4M13 11h4M7 15h4M13 15h4M7 19h4M13 19h4" stroke="#e42328" stroke-width="1.8"/></svg>
  </div>
  <div class="abs benefit benefit--grey" style="left:384px">
    <h3>AFFORDABLE<br>SOLUTIONS</h3>
    <p>Lowest Out of Pocket<br>Costs for Your Customers.</p>
    <svg viewBox="0 0 24 24" aria-hidden="true"><circle cx="13" cy="8" r="4.5" fill="none" stroke="#e42328" stroke-width="1.8"/><path d="M2 18 C6 15 9 15 12 17 L18 16 C20 16 21 18 19 19 L11 22 L2 21 Z" fill="#e42328"/></svg>
  </div>
  <div class="abs benefit benefit--framed" style="left:553px">
    <h3>INDUSTRY<br>LEADERS</h3>
    <p>Licensed &amp; Certified Experts<br>Provide 100% Guarantee.</p>
    <svg viewBox="0 0 24 24" aria-hidden="true"><circle cx="12" cy="7" r="2.5" fill="#e42328"/><circle cx="6" cy="9" r="2" fill="#e42328"/><circle cx="18" cy="9" r="2" fill="#e42328"/><path d="M3 14 H21 V16 H3 Z" fill="#e42328"/><path d="M5 18 A7 5 0 0 0 19 18" fill="none" stroke="#e42328" stroke-width="1.8"/></svg>
  </div>

  <p class="abs slogan">SEND REFERRALS. GET PAID.<br>GROW YOUR BUSINESS.</p>
  <div class="abs contact">
    <div class="label">CALL, TEXT OR<br>BOOK ONLINE</div>
    <div class="lines">
      <div class="phone">858-471-6093</div>
      <div class="web">BrightlaneRenovate.com</div>
    </div>
  </div>
</section>

<!-- BACK SIDE -->
<section class="card card--back">
  <div class="abs back-band"></div>
  <svg class="abs cash-photo" viewBox="0 0 757 192" role="img" aria-label="Photo of hundred-dollar bills with letter tiles spelling cash flow">
    <defs>
      <linearGradient id="bills" x1="0" y1="0" x2="1" y2="1">
        <stop offset="0" stop-color="#d6dad4"/>
        <stop offset="0.5" stop-color="#b9c2bd"/>
        <stop offset="1" stop-color="#8e9896"/>
      </linearGradient>
    </defs>
    <polygon points="348,0 365,0 392,112" fill="#4b73e8"/>
    <polygon points="365,0 757,0 757,192 408,192" fill="url(#bills)" stroke="#ffffff" stroke-width="2"/>
  </svg>

  <svg class="abs refer-shadow" viewBox="0 0 757 230" aria-hidden="true">
    <polygon points="185,36 238,76 238,219 125,219 71,176 185,176" fill="#0a1426"/>
  </svg>
  <h2 class="abs refer-stack">
    <span class="small">The more you</span>
    <span class="big">Refer</span>
    <span class="small">The more you</span>
    <span class="big">Earn</span>
  </h2>
  <div class="abs how">HOW IT WORKS</div>

  <article class="abs step" style="left:77px">
    <svg class="photo" viewBox="0 0 194 125" role="img" aria-label="Photo of drying equipment set up in a flooded basement"><rect width="194" height="125" fill="#b5b1aa"/><rect y="70" width="194" height="55" fill="#5a9ec4" opacity="0.45"/></svg>
    <h4>REFER FLOOD, MOLD &amp;<br>CONSTRUCTION JOBS</h4>
    <p>It's Simple to <b>Refer 24/7:</b><br>Call, Text or Book Online.</p>
  </article>
  <article class="abs step" style="left:282px">
    <svg class="photo" viewBox="0 0 194 125" role="img" aria-label="Photo of an inspector holding a work estimate in front of a house"><rect width="194" height="125" fill="#9aa7ae"/><rect y="80" width="194" height="45" fill="#6f8a5c" opacity="0.6"/></svg>
    <h4>WE TAKE CARE OF<br>EVERYTHING</h4>
    <p>We Schedule a <b>Free<br>Estimate.</b> If Approved,<br>You <b>Get Paid.</b></p>
  </article>
  <article class="abs step" style="left:487px">
    <svg class="photo" viewBox="0 0 194 125" role="img" aria-label="Photo of a yellow road sign reading get paid to share against a cloudy sky"><defs><linearGradient id="sky" x1="0" y1="0" x2="0" y2="1"><stop offset="0" stop-color="#4f8fd6"/><stop offset="1" stop-color="#c9dcef"/></linearGradient></defs><rect width="194" height="125" fill="url(#sky)"/></svg>
    <h4>EVERYBODY BENEFITS<br>FROM REFERRALS</h4>
    <p>From Referrals We Provide<br><b>Expert Quality Work</b><br>for Affordable Price.</p>
  </article>
</section>

</body>
</html>
```